Business Card Design

We have recently seen two business cards that caught our attention and think the designs would work for us. We are an accounting firm that serves small businesses in a variety of industries. Attached are the two business card that inspired us along with very rough layouts. We would like to see a professional layout using our company information.

Industry/Entity Type

Accounting

Contact Information for Business Card

Company Name - Marlowe Thistle
Address - 4182 Orlanby Lane, Suite 610, Houston, TX 77093
713-555-0187 - Main
281-555-0342 - Fax

Team Member Names, emails and phone numbers (see attachment)

```html
<!DOCTYPE html>
<html lang="en">
<head>
<meta charset="utf-8">
<title>Marlowe Thistle – Business Card</title>
<link rel="stylesheet" href="https://fonts.googleapis.com/css2?family=Open+Sans:wght@400;600&display=swap">
<style>
  :root {
    --backdrop: #b5b5b5;
    --card-white: #ffffff;
    --ink-black: #0d0d0d;
    --panel-top: #1a1c1e;
    --panel-bottom: #050607;
    --silver-dark: #7d7f81;
    --silver-light: #f2f4f5;
    --name-grey: #b8b8b8;
    --text-white: #f4f4f4;
    --divider: #8a8c8e;
  }
  * { margin: 0; padding: 0; box-sizing: border-box; }
  html, body { width: 1200px; height: 900px; overflow: hidden; }
  body { background: var(--backdrop); font-family: "Open Sans", sans-serif; }
  .canvas { position: relative; width: 1200px; height: 900px; }

  .card {
    position: absolute; left: 59px; top: 104px;
    width: 1085px; height: 634px;
    background: var(--card-white);
    overflow: hidden;
  }
  .brand {
    position: absolute; left: 0; top: 0; width: 100%; height: 339px;
  }
  .brand-mark {
    position: absolute; left: 50%; top: 62px;
    width: 150px; height: 150px; margin-left: -75px;
    background: var(--ink-black);
  }
  .brand-name {
    position: absolute; left: 0; right: 0; top: 268px;
    text-align: center;
    font-size: 40px; font-weight: 600; letter-spacing: 2px;
    color: var(--ink-black); text-transform: uppercase; line-height: 1;
  }
  .silver-band {
    position: absolute; left: 0; top: 339px; width: 100%; height: 23px;
    background: linear-gradient(90deg, var(--silver-dark) 0%, var(--silver-light) 18%, #9a9c9e 38%, var(--silver-light) 58%, #8f9193 78%, var(--silver-light) 94%, var(--silver-dark) 100%);
  }
  .contact-panel {
    position: absolute; left: 0; top: 362px; width: 100%; height: 272px;
    background: linear-gradient(180deg, var(--panel-top), var(--panel-bottom));
    color: var(--text-white);
  }
  .person {
    position: absolute; right: 591px; top: 48px; text-align: right;
  }
  .person-name { font-size: 34px; font-weight: 600; color: var(--name-grey); line-height: 44px; }
  .person-title { font-size: 24px; line-height: 32px; }
  .person-phones { margin-top: 18px; font-size: 27px; line-height: 36px; }
  .divider {
    position: absolute; left: 539px; top: 42px; width: 2px; height: 184px;
    background: var(--divider);
  }
  .company {
    position: absolute; left: 584px; top: 60px; font-size: 27px; line-height: 36px;
  }
  .company-address { margin-top: 16px; }
  .label-pad { display: inline-block; width: 80px; }
</style>
</head>
<body>
<main class="canvas">
  <section class="card" aria-label="Marlowe Thistle business card">
    <header class="brand">
      <div class="brand-mark"></div>
      <div class="brand-name">Marlowe Thistle</div>
    </header>
    <div class="silver-band"></div>
    <div class="contact-panel">
      <div class="person">
        <div class="person-name">Delphine Arroway</div>
        <div class="person-title">Account Manager</div>
        <div class="person-phones">
          <div>Direct:&nbsp; 713-555-0129</div>
          <div>Mobile: 832-555-0176</div>
        </div>
      </div>
      <div class="divider"></div>
      <div class="company">
        <div>Main: 713-555-0187</div>
        <div><span class="label-pad">Fax:</span>281-555-0342</div>
        <div class="company-address">
          <div>4182 Orlanby Lane, Suite 610</div>
          <div>Houston, TX 77093</div>
        </div>
      </div>
    </div>
  </section>
</main>
</body>
</html>
```